Marlowe Group needs a business card

I would like the card to be simple but modern and elegant.
I like black and white.
or black and gold.
we are a private finance lender and also are involved in property and property developments.

please look at the business card photos i provided i would like M.G only one one side and all the other details on the other side use fonts that tie in with my theme.

Industry/Entity Type

Finance

Contact Information for Business Card

Marlowe Group (M.G) Daniel Marlowe M: 0413586207 E: danmarl@inboxmail.test

Font styles to use
Other font styles liked:
• Use fonts that would reflect our business

Colors
000000
ffffff

Requirements
Must have
• one side of details
• other side has either M.G or Marlowe Group like in the photos provided

```html
<!DOCTYPE html>
<html lang="en">
<head>
<meta charset="utf-8">
<title>Marlowe Group — Business Card</title>
<link rel="stylesheet" href="https://fonts.googleapis.com/css2?family=Cinzel:wght@400;700&family=Open+Sans:wght@400&display=swap">
<style>
  :root {
    --backdrop: #e9e6e1;
    --card-black: #0b0c0d;
    --card-black-soft: #17181a;
    --gold: #e8b41c;
    --gold-light: #f7d34a;
    --ink-white: #f4f4f4;
    --card-shadow: rgba(0, 0, 0, 0.28);
  }

  * { margin: 0; padding: 0; box-sizing: border-box; }

  html, body {
    width: 1200px;
    height: 900px;
    overflow: hidden;
    background: var(--backdrop);
  }

  .canvas {
    position: relative;
    width: 1200px;
    height: 900px;
  }

  .card {
    position: absolute;
    left: 290px;
    width: 620px;
    height: 355px;
    background: var(--card-black);
    box-shadow: 0 14px 30px var(--card-shadow);
    overflow: hidden;
  }

  /* Reverse side: monogram only */
  .card--back {
    top: 75px;
    display: flex;
    align-items: center;
    justify-content: center;
  }

  .monogram {
    font-family: "Cinzel", serif;
    font-weight: 400;
    font-size: 92px;
    letter-spacing: 6px;
    color: var(--gold);
    line-height: 1;
  }

  /* Front side: details */
  .card--front {
    top: 470px;
    background: radial-gradient(ellipse at 45% 35%, var(--card-black-soft) 0%, var(--card-black) 70%);
  }

  .company-name {
    position: absolute;
    left: 42px;
    top: 60px;
    font-family: "Cinzel", serif;
    font-weight: 400;
    font-size: 44px;
    letter-spacing: 1px;
    color: var(--gold);
    line-height: 1;
  }

  .front-monogram {
    position: absolute;
    right: 40px;
    top: 138px;
    font-family: "Cinzel", serif;
    font-weight: 400;
    font-size: 62px;
    letter-spacing: 4px;
    color: var(--gold);
    line-height: 1;
  }

  .person-name {
    position: absolute;
    left: 42px;
    top: 178px;
    font-family: "Cinzel", serif;
    font-weight: 700;
    font-size: 24px;
    letter-spacing: 1px;
    color: var(--gold);
    line-height: 1;
  }

  .contact-list {
    position: absolute;
    left: 44px;
    top: 248px;
    list-style: none;
    font-family: "Open Sans", sans-serif;
    font-size: 19px;
    color: var(--ink-white);
  }

  .contact-item {
    display: flex;
    align-items: center;
    gap: 10px;
    height: 30px;
  }

  .contact-icon {
    width: 16px;
    height: 18px;
    flex: none;
  }
</style>
</head>
<body>
<main class="canvas">

  <section class="card card--back" aria-label="Card reverse side">
    <span class="monogram">M.G</span>
  </section>

  <section class="card card--front" aria-label="Card front side">
    <h1 class="company-name">Marlowe Group</h1>
    <span class="front-monogram">M.G</span>
    <h2 class="person-name">Daniel Marlowe</h2>
    <ul class="contact-list">
      <li class="contact-item">
        <svg class="contact-icon" viewBox="0 0 16 18" aria-hidden="true">
          <rect x="3.5" y="1" width="9" height="16" rx="1.5" fill="none" stroke="var(--gold)" stroke-width="1.8"/>
          <line x1="6.5" y1="14" x2="9.5" y2="14" stroke="var(--gold)" stroke-width="1.4"/>
        </svg>
        <span>0413586207</span>
      </li>
      <li class="contact-item">
        <svg class="contact-icon" viewBox="0 0 16 18" aria-hidden="true">
          <rect x="0.5" y="4" width="15" height="10" fill="var(--gold)"/>
          <polyline points="0.8,4.5 8,10 15.2,4.5" fill="none" stroke="var(--card-black)" stroke-width="1.2"/>
        </svg>
        <span>danmarl@inboxmail.test</span>
      </li>
    </ul>
  </section>

</main>
</body>
</html>
```